Stationery Design Project

We are looking stationary Design for Velquin International, a high end clothing company. I have attached an image of our Logo below.
Updates
I am looking for designs for the following stationaries:
1. Leather Binders
2. Paper Binders
3. Letterhead
4. Envelopes
5. Pens, pencils etc
We would love to see designs with gold, black and white color combination.
Industry/Entity Type
Clothing
Look and feel
Each slider illustrates characteristics of the customer's brand and the style your logo design should communicate.

```html
<!DOCTYPE html>
<html lang="en">
<head>
<meta charset="utf-8">
<title>Velquin International — Letterhead</title>
<link rel="stylesheet" href="https://fonts.googleapis.com/css2?family=Cinzel:wght@600&display=swap">
<style>
  :root {
    --paper: #fcfbe9;
    --paper-shade: #f3f1dd;
    --ink: #0b0b0b;
    --silver: #c9c9c9;
    --silver-light: #e6e6e6;
    --white: #ffffff;
  }
  * { margin: 0; padding: 0; box-sizing: border-box; }
  html, body { width: 850px; height: 1200px; overflow: hidden; background: var(--paper); }
  .letterhead {
    position: relative;
    width: 850px;
    height: 1200px;
    overflow: hidden;
    background: var(--paper);
  }
  .letterhead__damask {
    position: absolute;
    inset: 185px 0 0 0;
    background: radial-gradient(ellipse at 50% 40%, var(--paper) 0%, var(--paper-shade) 100%);
  }
  .letterhead__crest-band {
    position: absolute;
    top: 0; left: 0;
    width: 850px;
    height: 152px;
    background: linear-gradient(90deg,
      var(--ink) 0%, #2a2a2a 18%, #6c6c6c 35%, var(--silver-light) 55%,
      var(--silver) 68%, #5a5a5a 82%, var(--ink) 100%);
  }
  .letterhead__ribbon {
    position: absolute;
    top: 150px; left: 0;
    width: 850px;
    height: 35px;
    background: linear-gradient(90deg,
      var(--ink) 0%, #1a1a1a 30%, #8a8a86 52%, #2b2b2b 64%, var(--ink) 100%);
  }
  .brand-badge {
    position: absolute;
    top: 68px;
    left: 323px;
    width: 204px;
    height: 162px;
    background: var(--ink);
    border-radius: 22px;
    box-shadow: 0 0 0 3px var(--paper);
    display: flex;
    flex-direction: column;
    align-items: center;
    justify-content: center;
  }
  .brand-badge::after {
    content: "";
    position: absolute;
    inset: 7px;
    border: 1.5px solid var(--white);
    border-radius: 16px;
  }
  .brand-badge__name,
  .brand-badge__suffix {
    font-family: "Cinzel", "Times New Roman", serif;
    font-weight: 600;
    color: var(--white);
    line-height: 1;
    text-align: center;
  }
  .brand-badge__name {
    font-size: 26px;
    letter-spacing: 2px;
    margin-top: 34px;
  }
  .brand-badge__suffix {
    font-size: 8px;
    letter-spacing: 4.5px;
    margin-top: 8px;
  }
</style>
</head>
<body>
  <main class="letterhead">
    <div class="letterhead__damask" role="img" aria-label="Faint repeating heraldic damask pattern on cream paper"></div>
    <div class="letterhead__crest-band" role="img" aria-label="Band of white line-drawn heraldic crests on a black to silver gradient"></div>
    <div class="letterhead__ribbon"></div>
    <div class="brand-badge">
      <span class="brand-badge__name">VELQUIN</span>
      <span class="brand-badge__suffix">INTERNATIONAL</span>
    </div>
  </main>
</body>
</html>
```